Irrigation Business needs their business cards modernised and revamped

I would like to keep my current logo, colours and revamp the format of the card.

I would like the card to be clean yet important.

Im not sure if you include texture but i would like the named logo to be indented into the card etc.

show me something alive and free something thats clinical to the point yet has a feel of achievement. i would like people to go nice card.

Target Market(s)

high end clients, corporate, sports field manger, the guys that make the decisions

Industry/Entity Type

Business

Contact Information for Business Card

nformation to be included

Dean Harlow (Director)
0487305526
dean@kolvat.biz
www.kestonfieldworks.com

instagram logo
google logo
facebook logo

Colors

Designer to choose colors to be used in the design.

Requirements
Nice to have
• indentations a really nice feel to the card good texture

```html
<!DOCTYPE html>
<html lang="en">
<head>
<meta charset="utf-8">
<title>Keston Fieldworks – Business Card</title>
<link rel="stylesheet" href="https://fonts.googleapis.com/css2?family=Roboto:wght@400;700;900&display=swap">
<style>
  :root {
    --backdrop: #e4e4e4;
    --card: #f7f7f7;
    --navy: #2f4a8a;
    --sky: #3d8fc7;
    --green: #13934a;
    --rule: #33509a;
    --text-light: #ffffff;
    --muted-white: #dfe5f2;
  }
  * { box-sizing: border-box; margin: 0; padding: 0; }
  html, body { width: 1200px; height: 576px; overflow: hidden; }
  body {
    background: var(--backdrop);
    font-family: "Roboto", Arial, sans-serif;
    position: relative;
  }
  .card {
    position: absolute;
    top: 140px;
    width: 484px;
    height: 292px;
    border-radius: 12px;
    background: var(--card);
    overflow: hidden;
    box-shadow: 0 3px 8px rgba(0,0,0,0.22);
  }
  .card--front { left: 82px; }
  .card--back { left: 634px; }

  /* front */
  .front-watermark {
    position: absolute;
    left: 286px; top: 29px;
    width: 208px; height: 208px;
    border-radius: 50%;
    border: 10px solid rgba(61,143,199,0.07);
    background: rgba(61,143,199,0.04);
  }
  .brand-mark {
    position: absolute;
    border-radius: 50%;
    background: var(--sky);
    border: 3px solid var(--navy);
  }
  .front-mark { left: 196px; top: 55px; width: 92px; height: 92px; }
  .brand-name {
    position: absolute;
    color: var(--navy);
    font-weight: 900;
    white-space: nowrap;
    letter-spacing: -0.3px;
  }
  .front-name {
    left: 0; right: 0; top: 158px;
    text-align: center;
    font-size: 27px;
  }
  .front-footer {
    position: absolute;
    left: 78px; width: 326px; top: 262px;
    height: 16px;
    display: flex; align-items: center; gap: 8px;
  }
  .front-footer .rule { flex: 1; height: 2px; background: var(--rule); }
  .social-dot {
    width: 15px; height: 15px; border-radius: 50%;
    background: var(--navy);
  }

  /* back */
  .back-band { position: absolute; left: 0; top: 0; }
  .back-mark { left: 68px; top: 33px; width: 80px; height: 80px; }
  .back-name { left: 166px; top: 58px; font-size: 24px; }
  .holder {
    position: absolute; left: 28px; top: 190px;
    color: var(--text-light);
  }
  .holder-name { font-size: 20px; font-weight: 700; letter-spacing: 0.2px; }
  .holder-role { font-size: 11px; margin-top: 3px; color: var(--muted-white); }
  .back-social {
    position: absolute; left: 28px; top: 244px;
    display: flex; gap: 5px;
  }
  .back-social .social-dot {
    width: 19px; height: 19px; background: var(--text-light);
  }
  .contact-list {
    position: absolute; left: 242px; top: 215px;
    list-style: none;
    color: var(--text-light);
    font-size: 12.5px;
  }
  .contact-list li {
    display: flex; align-items: center; gap: 9px;
    height: 17px;
  }
  .contact-list svg { width: 10px; height: 10px; fill: var(--text-light); flex: none; }
</style>
</head>
<body>

<section class="card card--front">
  <div class="front-watermark" role="img" aria-label="faint brand circle"></div>
  <div class="brand-mark front-mark" role="img" aria-label="brand mark"></div>
  <div class="brand-name front-name">KESTON FIELDWORKS</div>
  <div class="front-footer">
    <span class="rule"></span>
    <span class="social-dot" role="img" aria-label="social link"></span>
    <span class="social-dot" role="img" aria-label="social link"></span>
    <span class="social-dot" role="img" aria-label="social link"></span>
    <span class="rule"></span>
  </div>
</section>

<section class="card card--back">
  <svg class="back-band" width="484" height="292" viewBox="0 0 484 292">
    <path d="M0 160 Q242 112 484 160 L484 292 L0 292 Z" fill="var(--green)"/>
    <path d="M0 165 Q242 118 484 165 L484 292 L0 292 Z" fill="var(--navy)"/>
  </svg>
  <div class="brand-mark back-mark" role="img" aria-label="brand mark"></div>
  <div class="brand-name back-name">KESTON FIELDWORKS</div>

  <div class="holder">
    <div class="holder-name">DEAN HARLOW</div>
    <div class="holder-role">Director</div>
  </div>
  <div class="back-social">
    <span class="social-dot" role="img" aria-label="social link"></span>
    <span class="social-dot" role="img" aria-label="social link"></span>
    <span class="social-dot" role="img" aria-label="social link"></span>
  </div>

  <ul class="contact-list">
    <li>
      <svg viewBox="0 0 10 10" aria-hidden="true"><path d="M1 3 Q5 0 9 3 L8 4.5 L6.5 3.8 L6.5 3 Q5 2.6 3.5 3 L3.5 3.8 L2 4.5 Z M2.5 5 H7.5 L8.5 9 H1.5 Z"/></svg>
      <span>0487305526</span>
    </li>
    <li>
      <svg viewBox="0 0 10 10" aria-hidden="true"><path d="M0.5 2 H9.5 V8 H0.5 Z M1.2 2.6 L5 5.4 L8.8 2.6" stroke="var(--navy)" stroke-width="0.8"/></svg>
      <span>dean@kolvat.biz</span>
    </li>
    <li>
      <svg viewBox="0 0 10 10" aria-hidden="true"><circle cx="5" cy="5" r="4.2" fill="none" stroke="#fff" stroke-width="1"/><path d="M0.8 5 H9.2 M5 0.8 V9.2" stroke="#fff" stroke-width="0.8"/><ellipse cx="5" cy="5" rx="1.8" ry="4.2" fill="none" stroke="#fff" stroke-width="0.8"/></svg>
      <span>www.kestonfieldworks.com</span>
    </li>
  </ul>
</section>

</body>
</html>
```